Meal Plan Website Needs New Pages Designed

Brightwick Supper Kits is an online, membership based program that delivers weekly meal programs (7 days worth of recipes plus shopping lists) carefully crafted by an expert team of meal planners. All recipes are created to comply with the following macronutrient ratio: 65% healthy fats, 25% lean protein, 10% good carbs.
All recipes are Paleo friendly and a great resource for those individuals who want to correctly implement this type of diet.

We are re-designing our website and need the following pages designed:

· Home page w/ logo
· How it works page
· Get Started! page
· Recipes Page template (these will be the pages on our site that will have recipes)
· Kitchen Essentials Training page (this will be a page with videos and tips + tricks, PDFs, etc)

So 5 total PSDs, 1 for each page.

Target audience: Men and women between the ages of 30 and 60 who want to:
· Eat healthy
· Lose weight
· Follow/Implement the Paleo diet
· Take the guesswork out of preparing delicious AND healthy meals for them and their families
· Know exactly what to eat, what to buy, how to make it

Feelings/Messages we want to communicate through the design:
· “Organic” but elegant look
· Fresh/light/Airy
· Simple but NOT GENERIC
· “I want to get cooking” feeling

Our Stylistic preferences:
· Minimalist with a few bold elements (something in between)
· Easy to visually navigate (enough white space, but not too much)
· There is more to “see” than to “read”

Our Color Preferences:
· Lighter pallet
· Colors that evoke natural woods, granite countertops…
· Stay away from using all dark colors

Our Font Type Preferences:
· Easy to read
· Not more than 3 font types
· Not too rigid
· Not too sophisticated
· Simple with a touch

Examples of Website Designs that we like:
· http://www.dorvanta.com/meal-plans/
· http://grulvix.com/
· https://www.mistobarn.com/

```html
<!DOCTYPE html>
<html lang="en">
<head>
<meta charset="utf-8">
<title>Brightwick Supper Kits</title>
<link rel="stylesheet" href="https://fonts.googleapis.com/css2?family=Open+Sans:ital,wght@0,400;0,600;0,700;1,400;1,600&display=swap">
<style>
:root{
  --orange:#ef8f5c;
  --orange-soft:#f3a57c;
  --salmon:#eeb29b;
  --light-grey:#ebebeb;
  --white:#ffffff;
  --ink:#1f1f1f;
  --body-ink:#4a4a4a;
  --footer-bg:#7b7b7b;
  --footer-line:#8d8d8d;
}
*{margin:0;padding:0;box-sizing:border-box}
html,body{width:1200px;height:2308px;overflow:hidden}
body{font-family:"Open Sans",Arial,sans-serif;color:var(--ink);background:var(--white);position:relative}
section,header,footer{position:absolute;left:0;width:1200px}
.abs{position:absolute}

/* header */
.site-header{top:0;height:157px;background:var(--white)}
.brand{left:140px;top:40px;display:flex;align-items:center;gap:12px}
.brand-dot{width:34px;height:34px;border-radius:50%;background:var(--orange)}
.brand-name{font-size:24px;font-weight:600;color:var(--orange);line-height:1.15;width:180px}
.social{left:916px;top:37px;display:flex;gap:9px}
.social span{width:24px;height:24px;border-radius:50%;background:var(--orange)}
.main-nav{top:97px;left:0;width:1200px;font-size:14px;color:var(--orange);text-transform:uppercase}
.main-nav a{position:absolute;color:inherit;text-decoration:none;white-space:nowrap}
.nav-sep{left:1025px;top:92px;width:1px;height:20px;background:#9a9a9a}
.search{left:1038px;top:92px}

/* hero */
.hero{top:157px;height:420px;background:linear-gradient(120deg,#6c9a3a 0%,#d9472e 30%,#3f5a2a 48%,#e9e3d4 60%,#8cb345 75%,#cf3a2a 100%)}
.hero-photo{position:absolute;inset:0}
.hero-card{left:131px;top:106px;width:414px;height:208px;background:rgba(235,235,235,.72);padding:28px 0 0 58px}
.hero-card p{font-size:37px;font-style:italic;line-height:46px;color:#111}
.hero-card b{font-style:normal;font-weight:700}
.hero-card p:nth-child(2){padding-left:11px}
.hero-arrow{top:196px;font-size:20px;color:#fff}
.hero-dots{left:585px;top:407px;display:flex;gap:4px}
.hero-dots span{width:6px;height:6px;border-radius:50%;background:rgba(255,255,255,.6)}
.hero-dots span:first-child{background:#fff}

/* intro */
.intro{top:577px;height:575px;background:var(--salmon)}
h2{font-weight:400;font-size:29px;color:var(--ink)}
.intro h2{position:absolute;left:151px;top:74px}
.copy{font-size:11px;line-height:20px;color:var(--body-ink);text-align:justify}
.intro .copy{position:absolute;left:151px;top:128px;width:569px}
.copy p+p{margin-top:20px}
.intro-photo{left:745px;top:134px;width:301px;height:237px;border-radius:3px;background:linear-gradient(135deg,#e9c46a,#e77a3f 45%,#c93a2e 70%,#2f3352)}
.join-btn{left:152px;top:452px;width:228px;height:42px;background:linear-gradient(#3a3a3a,#0c0c0c);border:1px solid #555;color:#fff;font-size:17px;font-weight:600;display:flex;align-items:center;justify-content:center}

/* how it works */
.how{top:1152px;height:577px;background:var(--light-grey)}
.how h2{position:absolute;left:151px;top:54px}
.how .copy{position:absolute;left:151px;top:110px;width:895px}
.meal{position:absolute;top:334px;width:171px;text-align:center}
.meal-photo{width:171px;height:154px}
.meal-name{font-size:18px;margin-top:8px;color:#222}

/* testimonials */
.testimonials{top:1729px;height:277px;background:var(--white)}
.testimonials h2{position:absolute;left:151px;top:57px}
.t-nav{left:1016px;top:66px;font-size:20px}
.testimonials .copy{position:absolute;left:151px;top:114px;width:895px}
.author{left:151px;top:192px;font-size:13px;color:#333}

/* footer */
.site-footer{top:2006px;height:302px;background:var(--footer-bg);color:#fff}
.f-head{font-size:19px;top:40px}
.f-list{font-size:11px;line-height:20px;top:84px}
.f-list a{color:#fff;text-decoration:none;display:block}
.f-nav{left:626px;top:38px;font-size:19px;white-space:nowrap}
.newsletter{left:872px;top:87px;font-size:14px}
.newsletter small{display:block;font-size:11px;margin-top:10px}
.news-form{left:870px;top:144px;width:176px;height:18px;background:#fff;border-radius:9px}
.news-form span{position:absolute;left:12px;top:2px;font-size:10px;color:#aaa}
.news-form b{position:absolute;right:0;top:0;width:66px;height:18px;border-radius:9px;background:var(--orange);font-size:10px;font-weight:700;display:flex;align-items:center;justify-content:center;color:#fff}
.x1{left:1118px;top:120px;font-size:13px}
.f-rule{left:0;top:202px;width:1200px;height:1px;background:var(--footer-line)}
.legal{left:151px;top:237px;font-size:11px;line-height:20px}
</style>
</head>
<body>

<header class="site-header">
  <div class="brand abs"><span class="brand-dot"></span><span class="brand-name">Brightwick Supper Kits</span></div>
  <div class="social abs"><span></span><span></span><span></span><span></span><span></span></div>
  <nav class="main-nav abs">
    <a style="left:412px">Meal Plans</a>
    <a style="left:557px">About</a>
    <a style="left:666px">How It Works</a>
    <a style="left:831px">Resources</a>
    <a style="left:972px">Blog</a>
  </nav>
  <span class="nav-sep abs"></span>
  <svg class="search abs" width="24" height="22" viewBox="0 0 24 22"><circle cx="9" cy="8" r="6" fill="none" stroke="#9a9a9a" stroke-width="2"/><line x1="13.5" y1="12" x2="22" y2="19" stroke="#9a9a9a" stroke-width="3"/></svg>
</header>

<section class="hero">
  <div class="hero-photo" role="img" aria-label="Fresh salad with lettuce, tomato, cucumber, olives and feta"></div>
  <div class="hero-card abs">
    <p><b>65%</b> healthy fats</p>
    <p><b>25%</b> lean protein</p>
    <p><b>10%</b> good carbs</p>
  </div>
  <span class="hero-arrow abs" style="left:14px">&lt;</span>
  <span class="hero-arrow abs" style="left:1168px">&gt;</span>
  <div class="hero-dots abs"><span></span><span></span><span></span><span></span></div>
</section>

<section class="intro">
  <h2>Brightwick Supper Kits</h2>
  <div class="copy">
    <p>We provide membership based program that delivers weekly meal programs (7 days worth of recipes plus shopping lists) carefully crafted by an expert team of meal planners. All recipes are created to comply with the following macronutrient ratio: 65% healthy fats, 25% lean protein, 10% good carbs.</p>
    <p>Sed ut perspiciatis unde omnis iste natus error sit voluptatem accusantium doloremque laudantium, totam rem aperiam, eaque ipsa quae ab illo inventore veritatis et quasi architecto beatae vitae dicta sunt explicabo. Nemo enim ipsam voluptatem quia voluptas sit aspernatur aut odit aut fugit, sed quia consequuntur magni dolores eos qui ratione voluptatem sequi nesciunt. Neque porro quisquam est, qui dolorem ipsum quia dolor sit amet, consectetur, adipisci velit, sed quia non numquam eius modi tempora incidunt ut labore et dolore magnam aliquam quaerat voluptatem. Ut enim ad minima veniam, quis nostrum exercitationem ullam corporis suscipit laboriosam, nisi ut aliquid ex ea commodi consequatur? Quis autem vel eum iure reprehenderit qui in ea voluptate velit esse quam nihil molestiae consequatur, vel illum qui dolorem eum fugiat quo voluptas nulla pariatur?</p>
  </div>
  <div class="intro-photo abs" role="img" aria-label="Chicken wrap with peppers and salad on a plate"></div>
  <div class="join-btn abs">Join Commuity</div>
</section>

<section class="how">
  <h2>How It Works</h2>
  <div class="copy">
    <p>We provide membership based program that delivers weekly meal programs (7 days worth of recipes plus shopping lists) carefully crafted by an expert team of meal planners. All recipes are created to comply with the following macronutrient ratio: 65% healthy fats, 25% lean protein, 10% good carbs.</p>
    <p>Sed ut perspiciatis unde omnis iste natus error sit voluptatem accusantium doloremque laudantium, totam rem aperiam, eaque ipsa quae ab illo inventore veritatis et quasi architecto beatae vitae dicta sunt explicabo. Nemo enim ipsam voluptatem quia voluptas sit aspernatur aut odit aut fugit, sed quia consequuntur magni dolores eos qui ratione voluptatem sequi nesciunt. Neque porro quisquam est, qui dolorem ipsum quia dolor sit amet, consectetur, adipisci velit, sed quia non numquam eius modi tempora incidunt ut labore et dolore magnam aliquam quaerat voluptatem. Ut enim ad minima veniam, quis nostrum exercitationem ullam corporis suscipit laboriosam, nisi ut aliquid ex ea commodi consequatur? Quis autem vel eum iure reprehenderit qui in ea voluptate velit esse quam nihil molestiae consequatur, vel illum qui dolorem eum fugiat quo voluptas nulla pariatur?</p>
  </div>
  <div class="meal" style="left:152px"><div class="meal-photo" role="img" aria-label="Breakfast plate with eggs and toast" style="background:linear-gradient(135deg,#c9473a,#f2c64e 50%,#d98b3a)"></div><div class="meal-name">Breakfast</div></div>
  <div class="meal" style="left:392px"><div class="meal-photo" role="img" aria-label="Lunch salad bowl on a table" style="background:linear-gradient(135deg,#8c7d6a,#e58a4a 50%,#6e9c4a)"></div><div class="meal-name">Lunch</div></div>
  <div class="meal" style="left:637px"><div class="meal-photo" role="img" aria-label="Grilled dinner with vegetables" style="background:linear-gradient(135deg,#2e2a24,#b07a3c 50%,#5d7a2e)"></div><div class="meal-name">Dinner</div></div>
  <div class="meal" style="left:874px"><div class="meal-photo" role="img" aria-label="Glasses of fresh fruit juice with fruit" style="background:linear-gradient(135deg,#f0a82e,#e8452f 55%,#7aa83a)"></div><div class="meal-name">Juices</div></div>
</section>

<section class="testimonials">
  <h2>Testimonials</h2>
  <span class="t-nav abs">&lt; &gt;</span>
  <div class="copy"><p>Sed ut perspiciatis unde omnis iste natus error sit voluptatem accusantium doloremque laudantium, totam rem aperiam, eaque ipsa quae ab illo inventore veritatis et quasi architecto beatae vitae dicta sunt explicabo. Nemo enim ipsam voluptatem quia voluptas sit aspernatur aut odit aut fugit, sed quia consequuntur magni dolores eos qui ratione voluptatem sequi nesciunt.</p></div>
  <p class="author abs">- M J Corrow</p>
</section>

<footer class="site-footer">
  <div class="f-head abs" style="left:151px">Recipes</div>
  <div class="f-list abs" style="left:151px"><a>Breakfast</a><a>Snack</a><a>Meat-only</a><a>Dessert</a></div>
  <div class="f-list abs" style="left:252px"><a>Lunch</a><a>Dinner</a><a>Sides</a><a>MORE</a></div>
  <div class="f-head abs" style="left:389px">Resources</div>
  <div class="f-list abs" style="left:389px"><a>Will I Lose Weight on Paleo</a><a>Mistobarn Food GuideFuel Guide for Athletes</a><a>Sampler Menu &amp; Meal Plan</a><a>Following MistobarnWhole Foods</a></div>
  <div class="f-nav abs">MEAL PLANS &nbsp;|&nbsp; ABOUT &nbsp;|&nbsp; HOW IT WORK &nbsp;|&nbsp; BLOG</div>
  <div class="newsletter abs">Newsletter Subscription<small>For Exciting Recipes &nbsp;SUBSCRIBE</small></div>
  <div class="news-form abs"><span>Email id...</span><b>SUBMIT</b></div>
  <span class="x1 abs">X1</span>
  <span class="f-rule abs"></span>
  <div class="legal abs">© 2014 Brightwick Supper Kits. All Rights Reserved.<br>The material on this site may not be reproduced, distributed, transmitted, cached, or otherwise used, except with the prior written permission of Brightwick Supper Kits.</div>
</footer>

</body>
</html>
```